Ledger Pulse (Ledger Pulse)

I need a design for Ledger Pulse application.
I would like to start from dark version of the design and the main goal that it should be pretty intuitive for everyone. I am going to create the app from scratch and I don't have any logo or branding colors, so it is up to you to choose a color scheme but it is a dark mode, so one of the colors would be black obviously.
The app will be available for web PC, Android and iOS.

There is google document with the requirements.
https://files.morvaly.net/page/d/7KpLsW2vQeR9tY4uZ1aBcD3fG5hJ8nM0xZ6oIqEw/view?mode=share

Target Market(s)

Professional traders

Industry/Entity Type

Trading

Colors

Designer to choose colors to be used in the design.

Requirements
Must have
• Dark mode design for PC and mobile views, the design must be pretty intuitive for everyone.
Nice to have
• Tooltips for something non obvious; popovers after completing some actions

```html
<!DOCTYPE html>
<html lang="en">
<head>
<meta charset="utf-8">
<title>Ledger Pulse – Account Setup</title>
<link href="https://fonts.googleapis.com/css2?family=Roboto:wght@400;500&display=swap" rel="stylesheet">
<style>
  :root {
    --bg: #0a0b14;
    --field: #12141f;
    --text: #ffffff;
    --label: #e6e7ee;
    --accent: #6a56c4;
    --accent-ink: #15122a;
    --photo-top: #6f8f8c;
    --photo-mid: #2b3a44;
    --photo-bottom: #1a2430;
  }
  * { box-sizing: border-box; margin: 0; padding: 0; }
  html, body { width: 1200px; height: 691px; overflow: hidden; background: var(--bg); }
  .canvas {
    position: relative; width: 1200px; height: 691px; overflow: hidden;
    background: radial-gradient(ellipse at 75% 40%, #141626 0%, var(--bg) 60%);
    font-family: "Roboto", Arial, sans-serif; color: var(--text);
  }
  .hero-photo {
    position: absolute; left: 0; top: 0; width: 550px; height: 691px;
    border-radius: 0 30px 30px 0;
    background:
      radial-gradient(ellipse at 75% 55%, rgba(214,170,160,0.45) 0%, rgba(214,170,160,0) 35%),
      linear-gradient(160deg, var(--photo-top) 0%, var(--photo-mid) 45%, var(--photo-bottom) 100%);
  }
  .brand {
    position: absolute; left: 609px; width: 540px; top: 178px; height: 44px;
    display: flex; align-items: center; justify-content: center; gap: 14px;
  }
  .brand-dot { width: 36px; height: 36px; border-radius: 50%; background: var(--accent); }
  .brand-name {
    font-family: "Roboto", Arial, sans-serif; font-weight: 500;
    font-size: 33px; line-height: 1; color: var(--text);
  }
  .setup-form { position: absolute; left: 609px; top: 0; width: 540px; height: 691px; }
  .field { position: absolute; width: 257px; }
  .field-label { display: block; font-size: 10px; line-height: 12px; color: var(--label); margin-bottom: 13px; }
  .field-box {
    height: 41px; background: var(--field); border-radius: 2px;
    display: flex; align-items: center; justify-content: space-between;
    padding: 0 16px 0 24px; font-size: 10px; color: var(--text);
  }
  .col-a { left: 0; } .col-b { left: 283px; }
  .row-1 { top: 276px; } .row-2 { top: 376px; }
  .send-button {
    position: absolute; left: 215px; top: 476px; width: 110px; height: 31px;
    border: 0; border-radius: 16px; background: var(--accent);
    color: var(--accent-ink); font-family: "Roboto", Arial, sans-serif;
    font-weight: 500; font-size: 11px;
  }
</style>
</head>
<body>
<div class="canvas">
  <div class="hero-photo" role="img" aria-label="Trader in a suit touching a floating holographic line chart"></div>

  <div class="brand">
    <span class="brand-dot"></span>
    <span class="brand-name">Ledger Pulse</span>
  </div>

  <form class="setup-form">
    <div class="field col-a row-1">
      <span class="field-label">Enter Display Name</span>
      <div class="field-box">Daniel Rourke</div>
    </div>
    <div class="field col-b row-1">
      <span class="field-label">What is your default account currency?</span>
      <div class="field-box">USD
        <svg width="7" height="10" viewBox="0 0 7 10"><path d="M3.5 0L7 4H0Z M3.5 10L7 6H0Z" fill="#fff"/></svg>
      </div>
    </div>
    <div class="field col-a row-2">
      <span class="field-label">What is your default time zone?</span>
      <div class="field-box">Time zone for the UI
        <svg width="7" height="10" viewBox="0 0 7 10"><path d="M3.5 0L7 4H0Z M3.5 10L7 6H0Z" fill="#fff"/></svg>
      </div>
    </div>
    <div class="field col-b row-2">
      <span class="field-label">What is your trading experience?</span>
      <div class="field-box">Beginner ( 0-1 years )
        <svg width="7" height="10" viewBox="0 0 7 10"><path d="M3.5 0L7 4H0Z M3.5 10L7 6H0Z" fill="#fff"/></svg>
      </div>
    </div>
    <button type="button" class="send-button">Send Message</button>
  </form>
</div>
</body>
</html>
```